Medical Device Packaging Project 4 of 5

We are a medical device startup company needing packaging for a total of 5 device brands. This is posting 4 of 5 and the device name is "Velonta"

Velonta is an intraocular lens for use in cataract surgery. The target market is Chinese ophthalmologists. The box should be sophisticated and upmarket.

The company name is Brenik Optics, I have included the logo in the uploaded files section. You should include the logo on the box.

I have uploaded a sample lens boxes from other companies that demonstrate the information needed to be contained on the box in terms of address, warnings, symbols, etc.

I have also uploaded the blank dieline of the boxes

You are welcome and encouraged to also submit to projects 1, 2, 3, and 5 as well. The same rules and expectations apply.

Industry/Entity Type

It Company

Requirements
Should not have
• Should not have any images of an eye or any bionic/futuristic feel to the design
• Note that the calvisto box is for text reference only. You may use the lens image but the futuristic/bionic look is NOT what we are going for with this brand. It should be traditional upmarket medical device artwork.

```html
<!DOCTYPE html>
<html lang="en">
<head>
<meta charset="utf-8">
<title>Velonta – Hydrophobic Intraocular Lens Packaging</title>
<link rel="stylesheet" href="https://fonts.googleapis.com/css2?family=Montserrat:wght@500;600&family=Arimo:wght@400&display=swap">
<style>
:root{
  --page:#ececec;
  --panel-top:#f7f6e6;
  --panel-bottom:#ece8bf;
  --olive:#9c9030;
  --navy:#1f3f72;
  --body-ink:#8a8130;
  --lens-light:#f4f4f4;
  --lens-mid:#b9b9b9;
  --lens-dark:#6f6f6f;
  --icon:#9a9a88;
}
*{margin:0;padding:0;box-sizing:border-box}
html,body{width:1200px;height:782px;overflow:hidden;background:var(--page)}
.canvas{position:relative;width:1200px;height:782px}
.panel{
  position:absolute;top:170px;width:540px;height:440px;overflow:hidden;
  background:linear-gradient(180deg,var(--panel-top) 0%,var(--panel-bottom) 100%);
  box-shadow:0 6px 18px rgba(0,0,0,.12);
}
.panel--back{left:30px}
.panel--front{left:630px}
.headline{position:absolute;right:26px;top:34px;width:300px;text-align:right;font-family:"Montserrat",sans-serif;font-weight:500;font-size:14px;line-height:1.4;color:var(--olive);text-transform:uppercase;letter-spacing:.02em}
.brand{position:absolute;left:36px;top:112px;display:flex;align-items:center;gap:9px}
.brand__dot{width:12px;height:12px;border-radius:50%;background:var(--navy)}
.brand__name{font-family:"Montserrat",sans-serif;font-weight:500;font-size:20px;letter-spacing:.06em;color:var(--navy);text-transform:uppercase;white-space:nowrap}
.lens{position:absolute;background:radial-gradient(circle at 45% 40%,var(--lens-light) 0%,var(--lens-mid) 45%,var(--lens-dark) 100%);border-radius:50%;opacity:.85}
.panel--back .lens{left:335px;top:170px;width:150px;height:150px}
.panel--front .lens{left:285px;top:125px;width:225px;height:225px}
.notices{position:absolute;left:36px;top:172px;width:260px;font-family:"Arimo",sans-serif;font-size:7.6px;line-height:1.15;color:var(--body-ink)}
.notices p{margin-bottom:3px}
.symbols{position:absolute;right:28px;bottom:26px;display:flex;gap:10px;align-items:center}
.symbols .sym-box{width:30px;height:14px;border:1px solid var(--icon)}
.symbols svg{width:14px;height:14px}
.product{position:absolute;left:36px;bottom:38px;font-family:"Montserrat",sans-serif;text-transform:uppercase}
.product__name{font-weight:600;font-size:22px;letter-spacing:.1em;color:var(--olive)}
.product__line{font-weight:500;font-size:15px;color:var(--olive);letter-spacing:.02em}
</style>
</head>
<body>
<main class="canvas">

  <section class="panel panel--back" aria-label="Box back panel">
    <h2 class="headline">Hydrophobic Intraocular Lens<br>Aspheric with 360° Lens</h2>
    <div class="brand"><span class="brand__dot"></span><span class="brand__name">Brenik Optics</span></div>
    <div class="lens" role="img" aria-label="Illustration of the intraocular lens with curved haptics"></div>
    <div class="notices">
      <p>Contains one sterile intraocular lens<br>Do not use if the packaging is damaged<br>Do not resterilize</p>
      <p>Bevat één steriele intraoculaire lens<br>Niet gebruiken als de verpakking beschadigd is<br>Niet opnieuw steriliseren</p>
      <p>Contient une lentille intraoculaire stérile<br>Ne pas utiliser si l'emballage est endommagé<br>Ne pas restériliser</p>
      <p>Enthält eine sterile intraokulare Linse<br>Nicht verwenden, wenn die Verpackung beschädigt ist<br>Nicht resterilisieren</p>
      <p>Periéchei éna apostei­roméno endofthálmio fakó<br>Μην το χρησιμοποιείτε εάν η συσκευασία έχει ζημιά<br>Μην επαναποστειρώνετε</p>
      <p>Contiene una lente intraoculare sterile<br>Non usare se la confezione è danneggiata<br>Non risterilizzare</p>
      <p>Contém uma lente intra-ocular esterilizada<br>Não use se a embalagem está danificada<br>Não reesterilize</p>
      <p>Contiene una lente intraocular estéril<br>No utilizar si el envase está dañado<br>No vuelva a esterilizar</p>
    </div>
    <div class="symbols" aria-label="Regulatory symbols">
      <span class="sym-box"></span>
      <svg viewBox="0 0 14 14"><path d="M7 1 L13 13 H1 Z" fill="none" stroke="var(--icon)"/></svg>
      <svg viewBox="0 0 14 14"><circle cx="7" cy="7" r="6" fill="none" stroke="var(--icon)"/><path d="M3 11 L11 3" stroke="var(--icon)"/></svg>
      <svg viewBox="0 0 14 14"><circle cx="7" cy="7" r="6" fill="none" stroke="var(--icon)"/><path d="M3 11 L11 3" stroke="var(--icon)"/></svg>
      <svg viewBox="0 0 14 14"><circle cx="7" cy="7" r="6" fill="none" stroke="var(--icon)"/><path d="M3 11 L11 3" stroke="var(--icon)"/></svg>
    </div>
  </section>

  <section class="panel panel--front" aria-label="Box front panel">
    <h2 class="headline">Hydrophobic Intraocular Lens</h2>
    <div class="brand"><span class="brand__dot"></span><span class="brand__name">Brenik Optics</span></div>
    <div class="lens" role="img" aria-label="Large illustration of the intraocular lens with curved haptics"></div>
    <div class="product">
      <div class="product__name">Velonta</div>
      <div class="product__line">Aspheric with 360° Lens</div>
    </div>
  </section>

</main>
</body>
</html>
```